BOLD & MINIMALIST DESIGN NEEDED

We want a very bold but minimalistic business card design that is impactful and utilizes both sides of the business card. Our current logo is included for your use.

We want bold fonts and good use of negative space. We don't want the logo to overpower the design.

Target Market(s)

Professionals who are building new commercial buildings.

Industry/Entity Type

Construction

Contact Information for Business Card

Name, Title, email, office phone, cell phone, website

Font styles to use
Serif
Sans Serif

Requirements
Must have
• Bold design!

```html
<!DOCTYPE html>
<html lang="en">
<head>
<meta charset="utf-8">
<title>Northvale Build – Business Card</title>
<link rel="stylesheet" href="https://fonts.googleapis.com/css2?family=Noto+Serif:wght@400;700&family=Source+Sans+3:wght@400;700&display=swap">
<style>
  :root {
    --backdrop: #a4fe7f;
    --card: #ffffff;
    --accent: #bafc88;
    --ink: #111111;
  }
  * { margin: 0; padding: 0; box-sizing: border-box; }
  html, body {
    width: 1200px;
    height: 1200px;
    overflow: hidden;
    background: var(--backdrop);
  }
  .canvas {
    position: relative;
    width: 1200px;
    height: 1200px;
    background: var(--backdrop);
  }
  .card {
    position: absolute;
    width: 631px;
    height: 361px;
    background: var(--card);
  }
  .card--front { left: 287px; top: 169px; }
  .card--back  { left: 281px; top: 686px; }

  .brand {
    position: absolute;
    display: flex;
    align-items: center;
    gap: 10px;
    transform: translate(-50%, -50%);
    font-family: "Source Sans 3", sans-serif;
    font-weight: 700;
    color: var(--ink);
    letter-spacing: 0.02em;
    white-space: nowrap;
  }
  .brand__mark {
    display: block;
    background: var(--accent);
  }
  .card--front .brand { left: 316px; top: 173px; font-size: 38px; }
  .card--front .brand__mark { width: 26px; height: 26px; }
  .card--back .brand { left: 507px; top: 171px; font-size: 21px; gap: 7px; }
  .card--back .brand__mark { width: 15px; height: 15px; }

  .accent-bar {
    position: absolute;
    background: var(--accent);
  }
  .card--front .accent-bar { left: 107px; top: 295px; width: 417px; height: 13px; }
  .accent-bar--title { left: 36px; top: 138px; width: 188px; height: 4px; }
  .accent-bar--brand { left: 414px; top: 249px; width: 188px; height: 3px; }

  .person__name {
    position: absolute;
    left: 36px;
    top: 66px;
    font-family: "Noto Serif", serif;
    font-weight: 700;
    font-size: 29px;
    color: var(--ink);
    white-space: nowrap;
  }
  .person__post {
    position: absolute;
    left: 43px;
    top: 100px;
    font-family: "Noto Serif", serif;
    font-weight: 400;
    font-size: 18px;
    color: var(--ink);
    white-space: nowrap;
  }
  .contact-list {
    position: absolute;
    left: 36px;
    top: 167px;
    list-style: none;
  }
  .contact-list__item {
    display: flex;
    align-items: center;
    height: 30px;
    font-family: "Source Sans 3", sans-serif;
    font-size: 24.5px;
    color: var(--ink);
    white-space: nowrap;
  }
  .contact-list__icon {
    width: 23px;
    height: 23px;
    margin-right: 10px;
    flex: none;
  }
</style>
</head>
<body>
<div class="canvas">
  <section class="card card--front">
    <div class="brand"><span class="brand__mark"></span>NORTHVALE BUILD</div>
    <div class="accent-bar"></div>
  </section>

  <section class="card card--back">
    <h1 class="person__name">YOUR NAME</h1>
    <p class="person__post">YOUR POST</p>
    <div class="accent-bar accent-bar--title"></div>

    <ul class="contact-list">
      <li class="contact-list__item">
        <svg class="contact-list__icon" viewBox="0 0 24 24" aria-hidden="true">
          <circle cx="12" cy="12" r="12" fill="var(--ink)"/>
          <path d="M6 11 Q12 6 18 11 L16.5 12.5 L14.5 11.5 L14.5 10 Q12 9 9.5 10 L9.5 11.5 L7.5 12.5 Z" fill="#fff"/>
          <rect x="8.5" y="12.5" width="7" height="4" rx="1" fill="#fff"/>
        </svg>
        Offic Phone
      </li>
      <li class="contact-list__item">
        <svg class="contact-list__icon" viewBox="0 0 24 24" aria-hidden="true">
          <circle cx="12" cy="12" r="12" fill="var(--ink)"/>
          <path d="M8 5.5 L10 9 L8.8 10.6 Q10 13.6 13.4 15.2 L15 14 L18.5 16 L17 18.6 Q10.5 18.5 5.4 7 Z" fill="#fff"/>
        </svg>
        Cell Phone
      </li>
      <li class="contact-list__item">
        <svg class="contact-list__icon" viewBox="0 0 24 24" aria-hidden="true">
          <rect x="0" y="4" width="24" height="16" rx="2" fill="var(--ink)"/>
          <polyline points="3,8 12,13 21,8" fill="none" stroke="#fff" stroke-width="1.6"/>
        </svg>
        Your Email Address
      </li>
      <li class="contact-list__item">
        <svg class="contact-list__icon" viewBox="0 0 24 24" aria-hidden="true">
          <circle cx="12" cy="12" r="11" fill="var(--ink)"/>
          <g fill="none" stroke="#fff" stroke-width="1.4">
            <line x1="1" y1="12" x2="23" y2="12"/>
            <line x1="12" y1="1" x2="12" y2="23"/>
            <ellipse cx="12" cy="12" rx="5" ry="11"/>
          </g>
        </svg>
        Your Website Address
      </li>
    </ul>

    <div class="brand"><span class="brand__mark"></span>NORTHVALE BUILD</div>
    <div class="accent-bar accent-bar--brand"></div>
  </section>
</div>
</body>
</html>
```